Hula-Hoop dance entertainment sales and instruction by spin-wavelet needs a business card

I need a 2 sided business card that is square (although this is not an absolute )for my self employed business as an independent artist. my business name is "Spin-Wavelet" I teach how to hula-hoop classes, make and sell hula-hoops, provided entertainment at kids birthday parties, community events, corporate events and perform at artistic dance shows.
I would like to see spirals or curved lines in the card, and I would like the card to be seen as fun, spunky, flair and eye catching.

the card could double as a tag to go on the hoops i sell,

Target Market(s)

women age 20 - 50

Industry/Entity Type

Entertainment

Requirements
Must have
• Dorine Vantash
www.spinwavelet.example
555.014.7263
Nice to have
• I would like my image to be on one side of the card. so people can recognize me!

```html
<!DOCTYPE html>
<html lang="en">
<head>
<meta charset="utf-8">
<title>Dorine Vantash — Spin-Wavelet Hoop Dance</title>
<link rel="stylesheet" href="https://fonts.googleapis.com/css2?family=Fredoka:wght@600&family=Questrial&family=Noto+Sans:wght@800&display=swap">
<style>
  :root {
    --card-lavender: #9ea3d3;
    --ink: #000000;
  }
  html, body {
    margin: 0;
    padding: 0;
    width: 1200px;
    height: 1200px;
    overflow: hidden;
    background: var(--card-lavender);
  }
  .card {
    position: relative;
    width: 1200px;
    height: 1200px;
    box-sizing: border-box;
    background: var(--card-lavender);
    border: 8px solid var(--ink);
  }
  .artist-name {
    position: absolute;
    left: 52px;
    top: 52px;
    width: 1080px;
    height: 152px;
    margin: 0;
    display: flex;
    align-items: center;
    justify-content: center;
    white-space: nowrap;
    font-family: "Fredoka", "Arial Rounded MT Bold", sans-serif;
    font-weight: 600;
    font-size: 120px;
    line-height: 1;
    letter-spacing: 2px;
    color: var(--ink);
  }
  .rule {
    position: absolute;
    left: 153px;
    width: 889px;
    height: 4px;
    background: var(--ink);
  }
  .rule--top { top: 254px; }
  .rule--bottom { top: 919px; }
  .services {
    position: absolute;
    left: 0;
    right: 0;
    top: 297px;
    margin: 0;
    padding: 0;
    list-style: none;
    text-align: center;
    font-family: "Questrial", "Century Gothic", sans-serif;
    font-size: 51px;
    line-height: 66px;
    color: var(--ink);
  }
  .contact {
    position: absolute;
    left: 0;
    right: 0;
    top: 966px;
    text-align: center;
    font-family: "Noto Sans", Verdana, sans-serif;
    font-weight: 800;
    font-size: 58px;
    line-height: 75px;
    color: var(--ink);
  }
  .contact p { margin: 0; }
</style>
</head>
<body>
  <main class="card">
    <h1 class="artist-name">Dorine Vantash</h1>
    <div class="rule rule--top"></div>
    <ul class="services">
      <li>Hoop Classes</li>
      <li>Hoop Jams</li>
      <li>Private Lessons</li>
      <li>Custom hula-hoops for adults and kids</li>
      <li>Performances</li>
      <li>Hoop Making Workshops</li>
      <li>Birthday Parties</li>
      <li>Corporate Event Entertainment</li>
      <li>and more!</li>
    </ul>
    <div class="rule rule--bottom"></div>
    <div class="contact">
      <p class="contact__web">www.spinwavelet.example</p>
      <p class="contact__phone">555.014.7263</p>
    </div>
  </main>
</body>
</html>
```